Design and Renovation Company Luxury Business Card

I want to create a luxury business card for a Design and Renovation Firm . We will use our current logo. The company name is 528BUILDA. We do not want anything standard. We need a very unique concept.
Please see uploaded inspiration. I really like the textured paper option. I would like the card to be thick with debossing, and/or embossing options. The logo has orange in it but I would like to see the card with and without the orange. I think the orange may make the company feel less high-end. The goal is to elevate the logo not match its vibe per se of the logo. We want something very unique, not standard at all!
I would like a space for :
Logo,
Name,
Position,
Email,
Office number,
Website Address,
Business Address,
Thank you!
Have fun!
Target Market(s)
Home owners Age 35 +
Industry/Entity Type
Design and Renovation
Contact Information for Business Card
Logo, Name, Position, Email, Office number, Website Address, Business Address,.
Colors
Designer to choose colors to be used in the design.
Requirements
Must have
- A luxury designer feel. Must be black or dark grey but open to other luxury ideas.
Nice to have
- Gold, silver, black embossing or debossing. Textured paper design.
Should not have
- A cheap look and feel.

```html
<!DOCTYPE html>
<html lang="en">
<head>
<meta charset="utf-8">
<title>528BUILDA Business Card</title>
<link href="https://fonts.googleapis.com/css2?family=Roboto:wght@400;700&display=swap" rel="stylesheet">
<style>
  :root {
    --backdrop: #e3e3e3;
    --card-front: #2f2f2f;
    --card-back: #2a2a2a;
    --orange: #e58a1c;
    --white: #f7f7f7;
    --text: #ffffff;
    --rule: #d9d9d9;
  }
  html, body {
    margin: 0;
    padding: 0;
    overflow: hidden;
  }
  body {
    width: 1200px;
    height: 1040px;
    background: var(--backdrop);
    font-family: "Roboto", Arial, sans-serif;
    position: relative;
  }
  .card {
    position: absolute;
    border-radius: 18px;
    overflow: hidden;
    color: var(--text);
  }
  .card-front { left: 285px; top: 130px; width: 641px; height: 368px; background: var(--card-front); }
  .card-back  { left: 284px; top: 567px; width: 646px; height: 370px; background: var(--card-back); }

  .brand {
    position: absolute;
    right: 42px;
    top: 44px;
    text-align: right;
  }
  .brand-name {
    font-size: 40px;
    font-weight: 400;
    line-height: 44px;
    letter-spacing: 0;
    color: var(--white);
  }
  .brand-tagline {
    font-size: 12px;
    font-weight: 400;
    letter-spacing: 2px;
    margin-top: 4px;
    color: var(--white);
  }

  .person {
    position: absolute;
    left: 45px;
    top: 198px;
  }
  .person-name {
    font-size: 26px;
    font-weight: 700;
    color: var(--orange);
    line-height: 30px;
  }
  .person-title {
    font-size: 17px;
    line-height: 20px;
  }
  .divider {
    position: absolute;
    left: 45px;
    width: 553px;
    top: 255px;
    height: 1px;
    background: var(--rule);
  }
  .contact {
    position: absolute;
    left: 45px;
    top: 266px;
    font-size: 16.5px;
    line-height: 20px;
  }
  .contact-line {
    display: flex;
    align-items: center;
    gap: 7px;
  }
  .contact-line svg { width: 12px; height: 12px; }
  .address {
    position: absolute;
    right: 43px;
    top: 268px;
    text-align: right;
    font-size: 16.5px;
    line-height: 20px;
  }
  .footer-bands {
    position: absolute;
    left: 0;
    bottom: 0;
    width: 641px;
    height: 42px;
  }
  .website {
    position: absolute;
    right: 38px;
    bottom: 11px;
    font-size: 16px;
    letter-spacing: 2px;
    color: var(--white);
  }

  .back-pattern {
    position: absolute;
    inset: 0;
    background: linear-gradient(90deg, #242424, #2b2b2b 60%, #2d2d2d);
  }
  .back-brand {
    position: absolute;
    right: 64px;
    top: 243px;
    font-size: 18px;
    font-weight: 400;
    color: var(--white);
  }
</style>
</head>
<body>

<section class="card card-front">
  <div class="brand">
    <div class="brand-name">528BUILDA</div>
    <div class="brand-tagline">Design and Renovation Firm</div>
  </div>

  <div class="person">
    <div class="person-name">Daniel Harper</div>
    <div class="person-title">President</div>
  </div>

  <div class="divider"></div>

  <div class="contact">
    <div class="contact-line">
      <svg viewBox="0 0 12 12" aria-hidden="true"><path d="M2.2 0.8 L4.2 0.6 L5 3.2 L3.8 4.2 C4.5 5.8 5.9 7.3 7.6 8.1 L8.6 6.9 L11.2 7.8 L11 9.8 C10.8 10.8 9.8 11.4 8.8 11.2 C4.9 10.4 1.4 7 0.7 3 C0.5 1.9 1.1 1 2.2 0.8 Z" fill="#e58a1c"/></svg>
      <span>(555) 0142-7788</span>
    </div>
    <div class="contact-line">
      <svg viewBox="0 0 12 12" aria-hidden="true"><rect x="0.5" y="2.5" width="11" height="7.5" fill="#e58a1c"/><path d="M0.8 3 L6 7 L11.2 3" stroke="#2f2f2f" stroke-width="1" fill="none"/></svg>
      <span>name@528BUILDA.com</span>
    </div>
  </div>

  <div class="address">
    <div>2710 Ashgrove Lane</div>
    <div>Cedar Hollow, NY 10999</div>
  </div>

  <svg class="footer-bands" viewBox="0 0 641 42" aria-hidden="true">
    <rect x="0" y="28" width="641" height="14" fill="#e58a1c"/>
    <polygon points="0,12 358,12 342,28 0,28" fill="#f7f7f7"/>
    <polygon points="371,0 641,0 641,42 330,42" fill="#e58a1c"/>
  </svg>
  <div class="website">www.528BUILDA.com</div>
</section>

<section class="card card-back">
  <div class="back-pattern" role="img" aria-label="Debossed repeating square pattern across the card back, fading from black to dark grey"></div>
  <div class="back-brand">528BUILDA</div>
</section>

</body>
</html>
```